Logo and Card design for KRV Home Solutions LLC

I need an edgier logo and business card designs. Current logo attached. I like the colors below. I would like the logo to incorporate a home in the design.
Title = Principal-Acquisitions
Email:KRVHOMESOLUTIONS@fernmail.example
555-214-0937
facebook
IG
2 sided business card with the front being contact info a slogan about selling a home fast. The back incorporating What we do. Buy houses, land, or commercial property as is. We find solutions to make the process of selling simple and fair.

Target Market(s)

Motivated house sellers.

Industry/Entity Type

Business

Contact Information for Business Card

Who we are: We are a Faith based Real Estate Investment Company. We pay cash for homes in any condition and can close quick. Whatever the reason you need to sell fast, we can help. We believe in creating win-win solutions to help you in your time of need. We care! We can help!

Logo Text

KRV Home Solutions LLC

Font styles to use
Sans Serif

Colors
33a6d7
0355a3
85abd2
cee9f5
9d9d9d
b2b2b2
ffffff

Requirements
Must have
• Old logo attached. I want something edgier.
• Company name, phone number, description on the back of what we can do. Pay all cash. Buy in as is condition. No fees,Commisions or closing costs.Close quick. No hassles with solutions to meet your unique situation.
• Call today for an offer within 24 hours.

```html
<!DOCTYPE html>
<html lang="en">
<head>
<meta charset="utf-8">
<title>Fernway Property Buyers – Business Card</title>
<link href="https://fonts.googleapis.com/css2?family=Roboto:wght@400;500;700&family=Roboto+Condensed:wght@400;700&display=swap" rel="stylesheet">
<style>
  :root {
    --stage: #2d2d2d;
    --card-dark: #1b2230;
    --photo-a: #3a4a5c;
    --photo-b: #2a3544;
    --photo-c: #4a5a4a;
    --royal: #1e4fd0;
    --navy: #24387a;
    --white: #ffffff;
    --paper: #f1f1f1;
    --body-grey: #474747;
    --rule: rgba(255,255,255,0.55);
  }
  * { margin: 0; padding: 0; box-sizing: border-box; }
  html, body { width: 1200px; height: 960px; overflow: hidden; }
  body { background: var(--stage); position: relative; font-family: "Roboto", sans-serif; }

  .card { position: absolute; width: 600px; height: 343px; overflow: hidden; box-shadow: 0 4px 10px rgba(0,0,0,0.45); }

  /* Front */
  .card-front { left: 314px; top: 113px; background: var(--card-dark); }
  .front-photo {
    position: absolute; inset: 0;
    background: linear-gradient(100deg, var(--photo-b) 0%, var(--photo-a) 45%, var(--photo-c) 100%);
  }
  .front-shade { position: absolute; inset: 0; background: rgba(15,20,30,0.6); }
  .front-brand {
    position: absolute; left: 30px; top: 150px; width: 220px; height: 34px;
    display: flex; align-items: center; justify-content: center; gap: 8px;
  }
  .brand-square { width: 12px; height: 12px; background: var(--royal); flex: none; }
  .front-brand .brand-name { color: var(--white); font-weight: 700; font-size: 17px; white-space: nowrap; }
  .front-divider { position: absolute; left: 257px; top: 58px; width: 1px; height: 240px; background: var(--rule); }
  .contact { position: absolute; left: 285px; top: 63px; color: var(--white); }
  .contact-name { font-family: "Roboto Condensed", sans-serif; font-weight: 700; font-size: 24px; line-height: 28px; color: var(--royal); letter-spacing: 0.3px; }
  .contact-title { font-weight: 500; font-size: 15px; line-height: 18px; }
  .contact-list { list-style: none; margin-top: 9px; }
  .contact-list li { display: flex; align-items: center; gap: 8px; font-size: 14.5px; height: 19px; white-space: nowrap; }
  .contact-list svg { width: 13px; height: 13px; fill: var(--royal); flex: none; }
  .offer-list { list-style: none; margin-top: 10px; font-family: "Roboto Condensed", sans-serif; font-size: 15px; line-height: 18px; }
  .offer-list li { position: relative; padding-left: 12px; white-space: nowrap; }
  .offer-list li::before { content: ""; position: absolute; left: 0; top: 7px; width: 4px; height: 4px; border-radius: 50%; background: var(--royal); }

  /* Back */
  .card-back { left: 311px; top: 472px; background: var(--paper); text-align: center; color: var(--body-grey); }
  .back-brand {
    position: absolute; left: 0; right: 0; top: 70px; height: 36px;
    display: flex; justify-content: center; align-items: center; gap: 10px;
  }
  .back-brand .brand-square { width: 14px; height: 14px; background: var(--navy); }
  .back-brand .brand-name { color: var(--navy); font-weight: 700; font-size: 26px; white-space: nowrap; }
  .back-copy { position: absolute; left: 0; right: 0; top: 168px; }
  .section-heading { color: var(--navy); font-weight: 700; font-size: 15.5px; line-height: 20px; }
  .section-text { font-size: 15.2px; line-height: 18px; white-space: nowrap; }
  .section-heading.second { margin-top: 12px; }
</style>
</head>
<body>

<section class="card card-front">
  <div class="front-photo" role="img" aria-label="Photo of a couple embracing in front of a two-storey house"></div>
  <div class="front-shade"></div>

  <div class="front-brand">
    <span class="brand-square"></span>
    <span class="brand-name">Fernway Property Buyers</span>
  </div>

  <div class="front-divider"></div>

  <div class="contact">
    <h1 class="contact-name">EVAN MARLOW</h1>
    <p class="contact-title">Principal-Acquisitions</p>
    <ul class="contact-list">
      <li><svg viewBox="0 0 24 24"><path d="M6.6 10.8a15.1 15.1 0 0 0 6.6 6.6l2.2-2.2c.3-.3.7-.4 1-.2 1.1.4 2.3.6 3.6.6.6 0 1 .4 1 1V20c0 .6-.4 1-1 1A17 17 0 0 1 3 4c0-.6.4-1 1-1h3.5c.6 0 1 .4 1 1 0 1.3.2 2.5.6 3.6.1.3 0 .7-.2 1z"/></svg>555-214-0937</li>
      <li><svg viewBox="0 0 24 24"><path d="M2 5h20v14H2zM4 7v.5l8 5 8-5V7l-8 5z"/></svg>KRVHOMESOLUTIONS@fernmail.example</li>
      <li><svg viewBox="0 0 24 24"><path d="M12 2a10 10 0 1 0 0 20 10 10 0 0 0 0-20zm6.9 6h-3a15 15 0 0 0-1.3-3.9A8 8 0 0 1 18.9 8zM12 4c.8 1.2 1.5 2.5 1.9 4h-3.8c.4-1.5 1.1-2.8 1.9-4zM4.3 14a8 8 0 0 1 0-4h3.4a16 16 0 0 0 0 4zm.8 2h3a15 15 0 0 0 1.3 3.9A8 8 0 0 1 5.1 16zm3-8h-3a8 8 0 0 1 4.3-3.9A15 15 0 0 0 8.1 8zM12 20c-.8-1.2-1.5-2.5-1.900-4h3.8c-.4 1.5-1.1 2.8-1.9 4zm2.3-6H9.7a14 14 0 0 1 0-4h4.6a14 14 0 0 1 0 4zm.3 5.9a15 15 0 0 0 1.3-3.9h3a8 8 0 0 1-4.3 3.9zm1.7-5.9a16 16 0 0 0 0-4h3.4a8 8 0 0 1 0 4z"/></svg>KRVHOMESOLUTIONS.example</li>
    </ul>
    <ul class="offer-list">
      <li>Pay all cash. Buy in as is condition</li>
      <li>No fees,Commisions or closing costs</li>
      <li>Close quick. No hassles with<br>solutions to meet your unique situation</li>
      <li>Call today for an offer within 24 hours</li>
    </ul>
  </div>
</section>

<section class="card card-back">
  <div class="back-brand">
    <span class="brand-square"></span>
    <span class="brand-name">Fernway Property Buyers</span>
  </div>

  <div class="back-copy">
    <h2 class="section-heading">WHO WE ARE</h2>
    <p class="section-text">We are a Faith based Real Estate Investment Company. We pay cash for<br>homes in any condition and can close quick. Whatever the reason you need<br>to sell fast, we can help. We believe in creating win-win solutions to help</p>

    <h2 class="section-heading second">WHAT WE DO</h2>
    <p class="section-text">Buy houses, land, or commercial property as is.<br>We find solutions to make the process of selling simple and fair.</p>
  </div>
</section>

</body>
</html>
```